Business Card Design for Training Business

Clear Path Coaching is a new business that delivers training and other services with a focus on topics related to mental health and wellbeing, for example, Wellmind Response Course, Resilience etc. We have a strong focus on evidence-based psychology and neuroscience. I have a logo which I will upload with the brief, so please consider colours that work well with the logo.
Target Market(s)
Adults, workplaces (particularly government and not-for-profits)
Industry/Entity Type
Business
Contact Information for Business Card
Head Strong TrainingSamantha SellwoodDirector0438 770 850sam@headstrongtraining.com.auwww.headstrongtraining.com.au

```html
<!DOCTYPE html>
<html lang="en">
<head>
<meta charset="utf-8">
<title>Clear Path Coaching – Business Card</title>
<link rel="stylesheet" href="https://fonts.googleapis.com/css2?family=Open+Sans:wght@300;400&display=swap">
<style>
  :root {
    --page-bg: #e9e8e6;
    --card-bg: #f7f7f7;
    --teal: #2fb7bb;
    --ink: #3e3e3e;
    --ink-soft: #6a6a6a;
    --brand-grey: #a3a3a3;
    --rule: #d6d6d6;
  }
  * { margin: 0; padding: 0; box-sizing: border-box; }
  html, body {
    width: 1200px;
    height: 1023px;
    overflow: hidden;
    background: var(--page-bg);
    font-family: "Open Sans", Arial, sans-serif;
  }
  .stage {
    width: 1200px;
    height: 1023px;
    display: flex;
    align-items: center;
    justify-content: center;
  }
  .business-card {
    position: relative;
    width: 1050px;
    height: 600px;
    background: linear-gradient(135deg, #fbfbfb 0%, var(--card-bg) 60%, #efefef 100%);
    box-shadow: 0 6px 22px rgba(0,0,0,0.12);
    overflow: hidden;
  }
  .edge-tab {
    position: absolute;
    width: 26px;
    height: 210px;
    background: var(--teal);
    border-radius: 8px;
  }
  .edge-tab--left { left: -12px; bottom: 70px; }
  .edge-tab--right { right: -12px; top: 30px; }

  .contact-side {
    position: absolute;
    left: 120px;
    top: 170px;
    width: 430px;
  }
  .person-name {
    font-weight: 400;
    font-size: 38px;
    color: var(--ink);
    letter-spacing: 0.2px;
  }
  .person-role {
    font-weight: 400;
    font-size: 27px;
    color: var(--teal);
    margin-top: 4px;
  }
  .company-name {
    font-weight: 400;
    font-size: 27px;
    color: var(--ink-soft);
    margin-top: 2px;
  }
  .contact-list {
    list-style: none;
    margin-top: 40px;
  }
  .contact-list li {
    display: flex;
    align-items: center;
    gap: 16px;
    font-weight: 300;
    font-size: 21px;
    color: var(--ink-soft);
    height: 36px;
  }
  .contact-icon {
    width: 20px;
    height: 20px;
    flex: none;
  }

  .card-divider {
    position: absolute;
    left: 600px;
    top: 150px;
    width: 1px;
    height: 300px;
    background: var(--rule);
  }

  .brand-side {
    position: absolute;
    left: 650px;
    top: 0;
    height: 600px;
    width: 360px;
    display: flex;
    align-items: center;
    gap: 22px;
  }
  .brand-dot {
    width: 110px;
    height: 110px;
    border-radius: 50%;
    background: var(--teal);
    opacity: 0.55;
    flex: none;
  }
  .brand-name {
    font-weight: 300;
    font-size: 30px;
    line-height: 1.2;
    letter-spacing: 2px;
    text-transform: uppercase;
    color: var(--brand-grey);
  }
</style>
</head>
<body>
<main class="stage">
  <article class="business-card">
    <span class="edge-tab edge-tab--left"></span>
    <span class="edge-tab edge-tab--right"></span>

    <section class="contact-side">
      <h1 class="person-name">Rebecca Tanfield</h1>
      <p class="person-role">Manager</p>
      <p class="company-name">Clear Path Coaching</p>
      <ul class="contact-list">
        <li>
          <svg class="contact-icon" viewBox="0 0 20 20" aria-hidden="true">
            <path d="M5 2 L8 2 L9 6 L7 8 Q9 12 12 13 L14 11 L18 12 L18 15 Q17 18 14 18 Q3 16 2 5 Q2 2 5 2 Z" fill="var(--teal)"/>
          </svg>
          0491 362 517
        </li>
        <li>
          <svg class="contact-icon" viewBox="0 0 20 20" aria-hidden="true">
            <rect x="1" y="4" width="18" height="12" rx="2" fill="var(--teal)"/>
            <path d="M2 5 L10 11 L18 5" stroke="#fff" stroke-width="1.5" fill="none"/>
          </svg>
          bec@clearpathcoaching.example.au
        </li>
        <li>
          <svg class="contact-icon" viewBox="0 0 20 20" aria-hidden="true">
            <circle cx="10" cy="10" r="9" fill="var(--teal)"/>
            <ellipse cx="10" cy="10" rx="4" ry="9" stroke="#fff" stroke-width="1.2" fill="none"/>
            <line x1="1" y1="10" x2="19" y2="10" stroke="#fff" stroke-width="1.2"/>
          </svg>
          www.clearpathcoaching.example.au
        </li>
      </ul>
    </section>

    <span class="card-divider"></span>

    <section class="brand-side">
      <span class="brand-dot"></span>
      <p class="brand-name">Clear Path<br>Coaching</p>
    </section>
  </article>
</main>
</body>
</html>
```